Dental Practice Billboard Design

We are a newer dental practice in need of a simple but appealing billboard for our growing dental practice to attract new patients. The practice is owned by husband and wife dentists and is family friendly in a small town in Kentucky. We try to be very friendly and caring to our patients. Would prefer a blue background for the billboard and our tooth logo to be prominent. We are partial to the Patua One font used in the image below but please feel free to tweak it as you deem necessary. The shape of the uppercase D and lowercase g are why we like that font, so fonts with a similarly shaped “D” and “g” would work as well. Please include our phone number (555) 847-1390. Please see our website Harlowbrookdentistry.example for more info on the practice if needed. Thank you! Looking forward to seeing your creation.
Updates

The dimensions will be 12ft x 24ft (3.6576m x 7.3152m). Apologies for not including this in the original prompt. Thank you all for your submissions.

Industry/Entity Type

Dental

Font styles to use
Other font styles liked:
• Patua One

Colors
0054AA
0677BA
7BADD7
CADEEF
E8F1F8
0094D4
00A9DD
6FCCEA
C7EBF8
E9F6FB
00AB8E
00BBA5
67D7C9
C6EFE9
E9F9F6
59FF00
82FF00
B8FF75
E3FFCB
F4FFEA

Requirements
Must have
• Phone number, website, Logo, Practice name “Harlow Brook Dentistry”
Should not have
• A tagline or slogan

```html
<!DOCTYPE html>
<html lang="en">
<head>
<meta charset="UTF-8">
<title>Harlow Brook Dentistry Billboard</title>
<link href="https://fonts.googleapis.com/css2?family=Patua+One&family=Montserrat:wght@800&display=swap" rel="stylesheet">
<style>
  :root {
    --navy: #0b2a5e;
    --navy-deep: #082453;
    --green: #17b21c;
    --green-bright: #1ec21f;
    --blue: #1156c0;
    --white: #ffffff;
    --stage: #eef2f6;
    --photo-warm: #c9a98c;
    --photo-light: #e9e2da;
  }
  * { margin: 0; padding: 0; box-sizing: border-box; }
  html, body {
    width: 1200px;
    height: 730px;
    overflow: hidden;
    background: var(--stage);
  }
  .billboard {
    position: absolute;
    left: 20px;
    top: 75px;
    width: 1160px;
    height: 580px;
    background: var(--white);
    overflow: hidden;
  }
  .brand-panel {
    position: absolute;
    left: 0;
    top: 0;
    width: 690px;
    height: 395px;
    background: linear-gradient(125deg, var(--navy-deep) 0%, var(--navy) 48%, var(--green) 92%);
    clip-path: polygon(0 0, 100% 0, 100% 100%, 0 100%);
  }
  .photo-area {
    position: absolute;
    left: 660px;
    top: 0;
    width: 500px;
    height: 580px;
  }
  .practice-name {
    position: absolute;
    left: 48px;
    top: 100px;
    display: flex;
    align-items: center;
    gap: 26px;
  }
  .name-dot {
    width: 92px;
    height: 92px;
    border-radius: 50%;
    background: var(--white);
    flex-shrink: 0;
  }
  .name-text {
    font-family: "Patua One", serif;
    color: var(--white);
    line-height: 1.05;
  }
  .name-main { display: block; font-size: 80px; }
  .name-sub { display: block; font-size: 50px; margin-left: 4px; }
  .contact {
    position: absolute;
    left: 20px;
    top: 408px;
  }
  .contact-row {
    display: flex;
    align-items: center;
    gap: 12px;
  }
  .phone {
    font-family: "Montserrat", sans-serif;
    font-weight: 800;
    font-size: 76px;
    line-height: 1.1;
    color: var(--navy);
    letter-spacing: 1px;
  }
  .website {
    margin-top: 4px;
    font-family: "Patua One", serif;
    font-size: 44px;
    line-height: 1.1;
    color: var(--navy);
  }
  .website .domain-end { color: var(--green); }
  .contact-icon { width: 34px; height: 34px; flex-shrink: 0; }
</style>
</head>
<body>
  <main class="billboard">
    <div class="brand-panel"></div>

    <svg class="photo-area" viewBox="0 0 500 580" aria-hidden="false">
      <defs>
        <clipPath id="photo-shape">
          <path d="M70 70 Q70 30 120 30 H390 Q440 30 440 80 V300 Q440 470 255 548 Q70 470 70 300 Z"/>
        </clipPath>
        <linearGradient id="photo-fill" x1="0" y1="0" x2="0.4" y2="1">
          <stop offset="0" stop-color="#e9e2da"/>
          <stop offset="1" stop-color="#c9a98c"/>
        </linearGradient>
      </defs>
      <path d="M30 0 H500 V420 L30 395 Z" fill="#1ec21f"/>
      <path d="M70 70 Q70 30 120 30 H390 Q440 30 440 80 V300 Q440 470 255 548 Q70 470 70 300 Z"
            fill="none" stroke="#ffffff" stroke-width="44"/>
      <path d="M255 548 Q70 470 70 300 V70 Q70 30 120 30 H250"
            fill="none" stroke="#1156c0" stroke-width="30" stroke-linecap="round"/>
      <path d="M255 548 Q440 470 440 300 V80 Q440 30 390 30 H260"
            fill="none" stroke="#17b21c" stroke-width="30" stroke-linecap="round"/>
      <path d="M70 70 Q70 30 120 30 H390 Q440 30 440 80 V300 Q440 470 255 548 Q70 470 70 300 Z"
            fill="none" stroke="#ffffff" stroke-width="6"/>
      <rect x="60" y="20" width="390" height="540" fill="url(#photo-fill)" clip-path="url(#photo-shape)"
            transform="translate(0 0) scale(1)" style="transform-box: fill-box; transform-origin: center; transform: scale(0.93);"
            role="img" aria-label="Photo of the two practice dentists, smiling, in white coats"/>
    </svg>

    <div class="practice-name">
      <span class="name-dot"></span>
      <span class="name-text">
        <span class="name-main">Harlow Brook</span>
        <span class="name-sub">Dentistry</span>
      </span>
    </div>

    <section class="contact">
      <div class="contact-row">
        <svg class="contact-icon" viewBox="0 0 24 24" aria-hidden="true">
          <path fill="#1156c0" d="M6.6 10.8a15.1 15.1 0 0 0 6.6 6.6l2.2-2.2a1 1 0 0 1 1-.25 11.4 11.4 0 0 0 3.6.57 1 1 0 0 1 1 1V20a1 1 0 0 1-1 1A17 17 0 0 1 3 4a1 1 0 0 1 1-1h3.5a1 1 0 0 1 1 1c0 1.25.2 2.45.57 3.57a1 1 0 0 1-.25 1z"/>
        </svg>
        <span class="phone">(555) 847-1390</span>
      </div>
      <div class="contact-row website">
        <svg class="contact-icon" viewBox="0 0 24 24" aria-hidden="true">
          <g fill="none" stroke="#1156c0" stroke-width="1.8">
            <circle cx="12" cy="12" r="10"/>
            <ellipse cx="12" cy="12" rx="4.5" ry="10"/>
            <line x1="2" y1="12" x2="22" y2="12"/>
            <line x1="4" y1="6.5" x2="20" y2="6.5"/>
            <line x1="4" y1="17.5" x2="20" y2="17.5"/>
          </g>
        </svg>
        <span>Harlowbrookdentistry<span class="domain-end">.example</span></span>
      </div>
    </section>
  </main>
</body>
</html>
```